Business card for marketing analytics company

Need a business card for new company. I have a logo already that I want to be built into the card and should use those colours

Company is called steered by tallies
Design must bring steered by tallies to life not be a card that could be for anyone with a logo put on it.

Like the front to be fairly clean and uncluttered bringing the logo out with a suitable design on the back of the card.

The logo represents a compass and business growth so those themes along with numbers, analytics , data are appropriate.
I'm often working with creative industries so also needs to reflect the creative side of analytics rather than be very corporate looking.

Target Market(s)

Ad agency, media agency, consumer goods clients

Industry/Entity Type

Market Research

Contact Information for Business Card

Needs to include name, title, email and phone number

Colors
f78f20
f68d4d
ec1f27

Requirements
Must have
• Must bring steered by tallies to life not be a card that could be for anyone with a logo put on it.
• Logo, Correct colours
• Like a design on the back that relates to company name
• Designs for both sides
Should not have
• Please do not just submit logo and a coloured card.
• It needs to have a design element to it
• No black background
• No clear cards - needs front & back

```html
<!DOCTYPE html>
<html lang="en">
<head>
<meta charset="utf-8">
<title>steered by tallies — business card</title>
<link rel="stylesheet" href="https://fonts.googleapis.com/css2?family=Exo+2:wght@400;500;700;800&display=swap">
<style>
  :root {
    --backdrop: #e4e1dc;
    --card: #faf7f2;
    --card-edge: #efe9e0;
    --red: #ec1f27;
    --deep-red: #c71c23;
    --orange: #f78f20;
    --coral: #f68d4d;
    --ink: #2b2b2d;
    --ink-soft: #5a5a5e;
    --grid: #e6ded2;
  }
  * { box-sizing: border-box; margin: 0; padding: 0; }
  html, body {
    width: 1200px; height: 1000px; overflow: hidden;
    background: var(--backdrop);
    font-family: "Exo 2", sans-serif;
  }
  .stage { position: relative; width: 1200px; height: 1000px; }

  .card {
    position: absolute;
    left: 280px;
    width: 640px; height: 366px;
    border-radius: 26px;
    background: linear-gradient(135deg, var(--card) 0%, var(--card) 55%, var(--card-edge) 100%);
    overflow: hidden;
    box-shadow: 0 18px 40px rgba(0,0,0,0.18);
  }
  .card--front { top: 90px; }
  .card--back { top: 530px; }

  /* data motif: plain grid, trend line and bars */
  .data-motif { position: absolute; display: block; }
  .card--front .data-motif { left: 0; bottom: 0; width: 640px; height: 120px; }
  .card--back .data-motif { right: 34px; top: 168px; width: 200px; height: 132px; }

  /* brand lockup */
  .brand { position: absolute; display: flex; align-items: center; }
  .brand__mark {
    border: 3px solid var(--red);
    border-radius: 50%;
    flex: none;
  }
  .brand__name {
    color: var(--orange);
    font-weight: 700;
    line-height: 1;
    white-space: nowrap;
  }
  .card--front .brand { left: 50%; top: 44%; transform: translate(-50%, -50%); gap: 22px; }
  .card--front .brand__mark { width: 96px; height: 96px; }
  .card--front .brand__name { font-size: 40px; }

  .card--back .brand { right: 34px; top: 92px; gap: 12px; }
  .card--back .brand__mark { width: 48px; height: 48px; border-width: 2px; }
  .card--back .brand__name { font-size: 21px; }

  /* person */
  .person { position: absolute; left: 44px; top: 60px; }
  .person__name {
    color: var(--red);
    font-weight: 800;
    font-size: 30px;
    letter-spacing: 0.5px;
    line-height: 1;
  }
  .person__title {
    margin-top: 8px;
    color: var(--ink);
    font-weight: 500;
    font-size: 17px;
    letter-spacing: 0.3px;
  }

  .address {
    position: absolute; left: 70px; top: 168px;
    color: var(--ink-soft);
    font-size: 14px; line-height: 1.35;
  }

  .contacts {
    position: absolute; left: 44px; top: 226px;
    list-style: none;
    color: var(--ink);
    font-size: 15px;
  }
  .contacts li { display: flex; align-items: center; gap: 12px; height: 22px; }
  .contacts svg { width: 14px; height: 14px; fill: var(--red); flex: none; }
  .contacts .accent { color: var(--red); }

  /* footer bands */
  .band { position: absolute; bottom: 0; }
  .band--red { left: 0; width: 460px; height: 28px; background: var(--deep-red); }
  .band--orange {
    left: 464px; right: 0; height: 28px;
    background: linear-gradient(90deg, var(--orange), var(--coral));
  }
</style>
</head>
<body>
<main class="stage">

  <section class="card card--front" aria-label="Card front">
    <svg class="data-motif" viewBox="0 0 640 120" aria-hidden="true">
      <g stroke="var(--grid)" stroke-width="1">
        <line x1="0" y1="30" x2="640" y2="30"/>
        <line x1="0" y1="60" x2="640" y2="60"/>
        <line x1="0" y1="90" x2="640" y2="90"/>
      </g>
      <polyline points="0,108 90,96 170,100 250,80 330,84 410,60 490,64 570,38 640,24"
                fill="none" stroke="var(--coral)" stroke-width="2.5" stroke-linejoin="round" opacity="0.7"/>
      <g fill="var(--orange)">
        <circle cx="250" cy="80" r="4"/><circle cx="410" cy="60" r="4"/><circle cx="570" cy="38" r="4"/>
      </g>
    </svg>
    <div class="brand">
      <span class="brand__mark"></span>
      <span class="brand__name">steered by tallies</span>
    </div>
  </section>

  <section class="card card--back" aria-label="Card back">
    <div class="person">
      <h1 class="person__name">DARIEN HOLT</h1>
      <p class="person__title">CEO/FOUNER</p>
    </div>

    <p class="address">Your Street Address,<br>Singapore, 1234</p>

    <ul class="contacts">
      <li>
        <svg viewBox="0 0 24 24" aria-hidden="true"><path d="M6.6 10.8a15.1 15.1 0 0 0 6.6 6.6l2.2-2.2a1 1 0 0 1 1-.25 11.4 11.4 0 0 0 3.6.57 1 1 0 0 1 1 1V20a1 1 0 0 1-1 1A17 17 0 0 1 3 4a1 1 0 0 1 1-1h3.5a1 1 0 0 1 1 1c0 1.25.2 2.45.57 3.57a1 1 0 0 1-.25 1z"/></svg>
        <span>+000 123 456 789</span>
      </li>
      <li>
        <svg viewBox="0 0 24 24" aria-hidden="true"><path d="M3 5h18v14H3z"/><path d="M3 6l9 7 9-7" fill="none" stroke="#faf7f2" stroke-width="2"/></svg>
        <span>yourname@email.com</span>
      </li>
      <li>
        <svg viewBox="0 0 24 24" aria-hidden="true"><circle cx="12" cy="12" r="10"/><path d="M2 12h20M12 2c3 3 3 17 0 20M12 2c-3 3-3 17 0 20" fill="none" stroke="#faf7f2" stroke-width="1.6"/></svg>
        <span>www.<span class="accent">websitename</span>.com</span>
      </li>
    </ul>

    <div class="brand">
      <span class="brand__mark"></span>
      <span class="brand__name">steered by tallies</span>
    </div>

    <svg class="data-motif" viewBox="0 0 200 132" aria-hidden="true">
      <line x1="0" y1="130" x2="200" y2="130" stroke="var(--grid)" stroke-width="2"/>
      <g>
        <rect x="8"   y="100" width="22" height="30" fill="var(--coral)" opacity="0.55"/>
        <rect x="46"  y="82"  width="22" height="48" fill="var(--coral)" opacity="0.7"/>
        <rect x="84"  y="64"  width="22" height="66" fill="var(--orange)" opacity="0.8"/>
        <rect x="122" y="40"  width="22" height="90" fill="var(--orange)"/>
        <rect x="160" y="16"  width="22" height="114" fill="var(--red)"/>
      </g>
      <polyline points="19,88 57,70 95,52 133,28 171,6" fill="none" stroke="var(--ink)" stroke-width="2" stroke-linejoin="round"/>
    </svg>

    <div class="band band--red"></div>
    <div class="band band--orange"></div>
  </section>

</main>
</body>
</html>
```